Shine Fox Auto Care Business Card

2 side business card design for an auto detailing business

Target Market(s)

Auto detailing

Contact Information for Business Card

Things included

The business name “Shine Fox Auto Care”
Mark Dunrow
(403)271-6094
Kelvale, Sk

Services offered - complete interior& exterior detail
- paint correction & protection
- ceramic coating
- trim restore
- auto carpet & seat cleaning

Requirements
Must have
• Colours that are in my logo

Services offered

My name Mark Dunrow
403-271-6094
Kelvale, Sk

Not too sure in what order for these ?
Website. Shinefoxautocare.com
Instagram Shinefoxautocare
Email. Shinefoxautoac@mailvento.com

```html
<!DOCTYPE html>
<html lang="en">
<head>
<meta charset="utf-8">
<title>Shine Fox Auto Care – Business Card</title>
<link href="https://fonts.googleapis.com/css2?family=Michroma&family=Montserrat:wght@400;500;700&display=swap" rel="stylesheet">
<style>
  :root {
    --brand-red: #980000;
    --ink: #111111;
    --paper: #ffffff;
    --backdrop: #8a8a8a;
  }
  html, body {
    margin: 0;
    padding: 0;
    width: 1200px;
    height: 1200px;
    overflow: hidden;
    background: var(--backdrop);
    font-family: "Montserrat", Arial, sans-serif;
  }
  .canvas {
    position: relative;
    width: 1200px;
    height: 1200px;
  }
  .card {
    position: absolute;
    left: 262px;
    width: 686px;
    height: 391px;
    border-radius: 20px;
    overflow: hidden;
    text-align: center;
  }
  .card--front { top: 165px; background: var(--paper); }
  .card--back { top: 653px; background: var(--brand-red); color: var(--paper); }

  .front-curve {
    position: absolute;
    inset: 0;
    width: 100%;
    height: 100%;
  }
  .brand {
    position: absolute;
    left: 0;
    right: 0;
    display: flex;
    flex-direction: column;
    align-items: center;
  }
  .brand-dot {
    border-radius: 50%;
    border-style: solid;
    box-sizing: border-box;
  }
  .brand-name {
    font-family: "Montserrat", Arial, sans-serif;
    font-weight: 700;
    text-transform: uppercase;
    line-height: 1.15;
    margin: 0;
  }
  .card--front .brand { top: 68px; }
  .card--front .brand-dot { width: 80px; height: 80px; border-width: 6px; border-color: var(--brand-red); }
  .card--front .brand-name { color: var(--brand-red); font-size: 24px; letter-spacing: 3px; margin-top: 14px; }

  .card--back .brand { top: 98px; }
  .card--back .brand-dot { width: 94px; height: 94px; border-width: 7px; border-color: var(--paper); }
  .card--back .brand-name { color: var(--paper); font-size: 28px; letter-spacing: 4px; margin-top: 16px; }

  .person {
    position: absolute;
    left: 0;
    right: 0;
    top: 308px;
    color: var(--paper);
  }
  .person-name {
    font-family: "Michroma", Arial, sans-serif;
    font-size: 21px;
    font-weight: 400;
    margin: 0;
    letter-spacing: 0.5px;
  }
  .person-contact {
    font-size: 16px;
    font-weight: 500;
    margin: 8px 0 0;
  }
  .services {
    position: absolute;
    left: 0;
    right: 0;
    top: 290px;
  }
  .services-title {
    font-size: 15.5px;
    font-weight: 700;
    margin: 0 0 8px;
    letter-spacing: 0.3px;
  }
  .services-list {
    font-size: 16.5px;
    font-weight: 400;
    line-height: 1.22;
    margin: 0;
    letter-spacing: 0.3px;
  }
  .bullet {
    display: inline-block;
    width: 7px;
    height: 7px;
    border-radius: 50%;
    background: var(--paper);
    vertical-align: middle;
    margin: 0 7px;
  }
</style>
</head>
<body>
<main class="canvas">

  <section class="card card--front" aria-label="Business card front">
    <svg class="front-curve" viewBox="0 0 686 391" preserveAspectRatio="none" aria-hidden="true">
      <path d="M0,172 Q343,390 686,164 L686,391 L0,391 Z" fill="var(--brand-red)"/>
      <path d="M0,166 Q343,383 686,158" fill="none" stroke="var(--ink)" stroke-width="4.5"/>
    </svg>
    <div class="brand">
      <span class="brand-dot"></span>
      <p class="brand-name">Shine Fox<br>Auto Care</p>
    </div>
    <div class="person">
      <h1 class="person-name">MARK DUNROW</h1>
      <p class="person-contact">Kelvale, Sk | (403)271-6094</p>
    </div>
  </section>

  <section class="card card--back" aria-label="Business card back">
    <div class="brand">
      <span class="brand-dot"></span>
      <p class="brand-name">Shine Fox<br>Auto Care</p>
    </div>
    <div class="services">
      <h2 class="services-title">COMPLETE INTERIOR &amp; EXTERIOR DETAIL</h2>
      <p class="services-list">
        Paint correction &amp; Protection<span class="bullet"></span>Ceramic coating<br>
        Trim restore<span class="bullet"></span>Auto carpet &amp; Seat cleaning
      </p>
    </div>
  </section>

</main>
</body>
</html>
```